Business Card

Just need business logo with phone number on it. 0487 312 654
And the following on the bottom of the card.

"Your local plumbing experts".
and emblems for zelpa card, cheque and cash

```html
<!DOCTYPE html>
<html lang="en">
<head>
<meta charset="utf-8">
<title>Ridgeway Plumbing &amp; Drainage – Business Card</title>
<link href="https://fonts.googleapis.com/css2?family=Russo+One&family=Orbitron:wght@800&family=Roboto:wght@300;400&display=swap" rel="stylesheet">
<style>
  :root {
    --backdrop: #2b2b2b;
    --card: #f4f4f2;
    --brand-red: #d5201c;
    --brand-blue: #0f7ac6;
    --white: #ffffff;
    --cheque: #f3ef8c;
    --cash: #5fa57a;
  }
  html, body {
    margin: 0;
    width: 1200px;
    height: 902px;
    overflow: hidden;
    background: var(--backdrop);
  }
  .card {
    position: absolute;
    left: 100px;
    top: 141px;
    width: 1000px;
    height: 620px;
    border-radius: 44px;
    background: var(--card);
    overflow: hidden;
  }
  .brand-name {
    position: absolute;
    right: 150px;
    top: 58px;
    margin: 0;
    font-family: "Russo One", sans-serif;
    font-weight: 400;
    color: var(--brand-red);
    text-align: right;
    line-height: 1;
  }
  .brand-name .primary { display: block; font-size: 74px; letter-spacing: 4px; }
  .brand-name .secondary { display: block; font-size: 33px; letter-spacing: 7px; margin-top: 10px; }
  .brand-suffix {
    position: absolute;
    right: 112px;
    top: 120px;
    font-family: "Roboto", sans-serif;
    font-size: 14px;
    letter-spacing: 2px;
    color: var(--brand-red);
    writing-mode: vertical-rl;
  }
  .band-art {
    position: absolute;
    left: 0;
    top: 250px;
  }
  .phone-row {
    position: absolute;
    left: 60px;
    top: 280px;
    display: flex;
    align-items: center;
    gap: 30px;
  }
  .phone-number {
    font-family: "Orbitron", sans-serif;
    font-weight: 800;
    font-size: 60px;
    letter-spacing: 4px;
    color: var(--white);
    white-space: nowrap;
  }
  .tagline {
    position: absolute;
    left: 250px;
    top: 376px;
    margin: 0;
    font-family: "Roboto", sans-serif;
    font-weight: 300;
    font-size: 30px;
    line-height: 36px;
    color: var(--white);
    white-space: nowrap;
  }
  .payment {
    position: absolute;
    left: 150px;
    top: 508px;
    display: flex;
    align-items: center;
    gap: 22px;
    font-family: "Roboto", sans-serif;
  }
  .payment-label { font-size: 26px; font-weight: 300; color: var(--brand-blue); }
  .payment-option {
    display: flex;
    align-items: center;
    justify-content: center;
    width: 82px;
    height: 44px;
    border-radius: 5px;
    font-size: 17px;
    font-weight: 400;
  }
  .payment-option.card-pay { border: 1.5px solid #b9c3d6; color: var(--brand-blue); background: var(--white); }
  .payment-option.cheque { background: var(--cheque); color: #6d6a2a; font-size: 12px; letter-spacing: 1px; }
  .payment-option.cash { background: var(--cash); color: var(--white); letter-spacing: 1px; }
</style>
</head>
<body>
  <main class="card">
    <h1 class="brand-name">
      <span class="primary">RIDGEWAY</span>
      <span class="secondary">PLUMBING &amp; DRAINAGE</span>
    </h1>
    <span class="brand-suffix">PTY LTD</span>

    <svg class="band-art" width="1000" height="270" viewBox="0 0 1000 270" aria-hidden="true">
      <rect x="0" y="0" width="1000" height="210" fill="var(--brand-red)"/>
      <polygon points="830,0 1000,0 1000,270 790,270" fill="var(--brand-blue)"/>
      <polygon points="790,210 830,0 830,210" fill="var(--brand-red)"/>
      <line x1="60" y1="138" x2="225" y2="138" stroke="var(--white)" stroke-width="3"/>
      <line x1="650" y1="160" x2="785" y2="160" stroke="var(--white)" stroke-width="3"/>
    </svg>

    <div class="phone-row">
      <svg width="58" height="58" viewBox="0 0 58 58" aria-label="Phone">
        <circle cx="29" cy="29" r="26" fill="none" stroke="var(--white)" stroke-width="4"/>
        <path d="M21 17c2-1 4 0 5 2l2 4c1 2 0 3-1 4l-2 1c1 3 4 6 7 7l1-2c1-1 2-2 4-1l4 2c2 1 3 3 2 5-1 3-4 4-7 3-8-2-15-9-17-17-1-3 0-6 2-8z" fill="var(--white)"/>
      </svg>
      <span class="phone-number">0487 312 654</span>
    </div>
    <p class="tagline">Your local plumbing experts</p>

    <div class="payment">
      <span class="payment-label">Payment made from:</span>
      <span class="payment-option card-pay">zelpa</span>
      <span class="payment-option cheque">CHEQUE</span>
      <span class="payment-option cash">CASH</span>
    </div>
  </main>
</body>
</html>
```